Velvet Loom (E-commerce) Website for Embroidery shop

Briefing:

Velvet Loom is an online personalized embroidery shop targeting mainly three customer segments:
1) lovers and marring couples
2) close friends wishing to give unique gifts
3) moms with new born baby personalized gifts

These customers are being served through our three major business lines:
1) Bathrobes and towels with personalized embroidery
2) Embroidered pillows and cushions
3) baby gifts with costumed baby sets stitched

Requirements:

The business has been recently established with moderate variety of products introduced so far. The website must consists of four major pages; a home page and three pages for every single business line. All images necessary for the web design are shareable upon request for copyright reasons if necessary. Please post a few products in each page to make it easy for the employee to use as benchmarks to upload other products.

The website also should contain all items and buttons exist in any e-commerce website such as:

1- social links:
a. (Major) Picturely: https://www.instagram.com/velvet.loom.studio/
b. Chirper: https://twitter.com/Velvet_Loom_
c. Friendbook: https://www.facebook.com/Velvet.loom.studio/
d. Snapchat: coming soon

2- Help:
a. Delivery & Returns (inside KSA)
I. Delivery:
- Rush: within 3 business days (SAR 90)
- Express: within 5 business days (SAR 65)
- Standard: 7-10 business days ( SAR 35)
II. Returns: We guarantee you will love our product. But if you don't like it, send it back to us within two days from delivery and we will donate it to a charity and return your money subject to our terms and conditions.

b. Contact:
- Email: Velvet.loom.studio@plumemail.net
- (Mobile) Whats-app: +966 54 312 9067 (for quick response)

d. Warranty:
for only SAR 20 per product, we will give you a lifetime warranty over our German stitches

3- Payment options:
bank transfer, visa, MasterCard and PayPal

Remarks:

- This website is mainly aimed at customers in Saudi Arabia where some contents may not appeal to people from such country and results in your participation being excluded from the contest.

- You are the expert and if I am a webdesigner, I would have not posted this contest, so please use your our own judgment and creativity to come up with the best experience possible.

- Use our Picturely account as your first reference to understand our business as it is our major channel that has been used to reach our customers. Please don't use the pictures with poor quality as we will be replacing them with other images with better quality.

- We intend to have this website bilingual (i.e English and Arabic), so if you can translate it into Arabic, then we will pay you an extra $100 in addition to the contest price.

- If in doubt, please feel free to ask any question and suggestions are always encouraged and warm welcomed.

- If you succeed in this contest, you will be chosen as our ultimate Web designer. That means you will have a long relationship providing services to our customers under one of our businesses that aims at preparing start-up companies establishing their business.

Target Market(s)

1) lovers and marrying couples

Industry/Entity Type

Embroidery

Number of Pages Required

4 page

Font styles to use
Serif
Script

Colors

Designer to choose colors to be used in the design.

Requirements
Must have
• Requirements:
• The business has been recently established with moderate variety of products introduced so far. The website must consists of four major pages; a home page and three pages for every single business line. All images necessary for the web design are shareable upon request for copyright reasons if necessary. Please post a few products in each page to make it easy for the employee to use as benchmarks to upload other products.
• The Website must be also mobile use friendly!!!
• The website also should contain all items and buttons exist in any e-commerce website such as:
• 1- social links:
• a. (Major) Picturely: https://www.instagram.com/velvet.loom.studio/
• b. Chirper: https://twitter.com/Velvet_Loom_
• c. Friendbook: https://www.facebook.com/Velvet.loom.studio/
• d. Snapchat: coming soon
• 2- Help:
• a. Delivery & Returns (inside KSA)
• I. Delivery:
• - Rush: within 3 business days (SAR 90)
• - Express: within 5 business days (SAR 65)
• - Standard: 7-10 business days ( SAR 35)
• II. Returns: We guarantee you will love our product. But if you don't like it, send it back to us within two days from delivery and we will donate it to a charity and return your money subject to our terms and conditions.
• b. Contact:
• - Email: Velvet.loom.studio@plumemail.net
• - (Mobile) Whats-app: +966 54 312 9067 (for quick response)
• d. Warranty:
• for only SAR 20 per product, we will give you a lifetime warranty over our German stitches
• 3- Payment options:
• bank transfer, visa, MasterCard and PayPal
• Note: You will be responsible to upload the design to the website fully and ensure its integration and functionality.

```html
<!DOCTYPE html>
<html lang="en">
<head>
<meta charset="utf-8">
<title>Velvet Loom — Personalized Embroidery</title>
<link rel="stylesheet" href="https://fonts.googleapis.com/css2?family=Roboto:wght@300;400;500&family=Open+Sans:wght@400;600;700&display=swap">
<style>
:root{
  --gold:#b8964f;
  --gold-soft:#c5a76c;
  --grey-dark:#6f6f6f;
  --grey-mid:#7d7d7d;
  --grey-btn:#7a7a7a;
  --grey-light:#eeeeee;
  --line:#dddddd;
  --text:#333333;
  --muted:#8a8a8a;
  --white:#ffffff;
}
*{box-sizing:border-box;margin:0;padding:0}
html,body{width:1200px;height:3550px;overflow:hidden}
body{position:relative;background:var(--white);font-family:"Open Sans",sans-serif;color:var(--text)}
.abs{position:absolute}
a{color:inherit;text-decoration:none}

/* top bar */
.topbar{left:0;top:0;width:1200px;height:47px;background:var(--grey-dark);color:var(--white);font-size:15px;font-family:"Roboto",sans-serif}
.topbar span{position:absolute;top:14px}
.topbar .lang{left:502px;font-size:12px;top:16px}
.cart{position:absolute;left:978px;top:0;width:122px;height:47px;background:var(--gold);display:flex;align-items:center;justify-content:center;gap:8px;font-size:15px}

/* header */
.header{left:0;top:47px;width:1200px;height:111px;background:var(--white)}
.brand-badge{position:absolute;left:102px;top:-22px;width:250px;height:160px;border-radius:50%;background:var(--white);box-shadow:0 3px 8px rgba(0,0,0,.18);z-index:5;display:flex;align-items:center;justify-content:center}
.brand-name{font-family:"Roboto",sans-serif;font-weight:500;color:var(--gold);font-size:34px;white-space:nowrap}
.nav{position:absolute;top:48px;font-family:"Roboto",sans-serif;font-size:16px;color:var(--muted);letter-spacing:.3px}
.nav.active{color:var(--text)}

/* hero */
.hero{left:0;top:158px;width:1200px;height:564px;overflow:hidden}
.hero-photo{position:absolute;inset:0;background:linear-gradient(120deg,#6f5a7c 0%,#8f7b99 30%,#d9d5d8 55%,#ece9ea 75%,#c9bfc6 100%)}
.hero-badge{position:absolute;left:715px;top:70px;width:340px;height:340px;border-radius:50%;background:var(--gold);border:6px solid rgba(255,255,255,.85);box-shadow:0 0 0 4px rgba(184,150,79,.5);color:var(--white);text-align:center;padding-top:112px}
.hero-badge h2{font-family:"Roboto",sans-serif;font-weight:300;font-size:34px;line-height:40px;white-space:nowrap}
.hero-badge p{font-size:12px;line-height:18px;margin:8px auto 0;width:250px;opacity:.9}
.btn-dark{display:inline-block;margin-top:20px;background:#5a5144;color:var(--white);border-radius:20px;font-size:14px;padding:8px 24px}
.dots{position:absolute;left:549px;top:452px;display:flex;gap:8px}
.dots i{width:12px;height:12px;border-radius:50%;border:2px solid var(--white)}
.dots i.on{background:var(--white)}
.hero-curve{position:absolute;left:0;bottom:0}

/* welcome */
.welcome-title{left:0;top:728px;width:1200px;text-align:center;font-family:"Roboto",sans-serif;font-weight:400;font-size:42px;color:var(--text)}
.welcome-text{left:190px;top:802px;width:820px;text-align:center;font-size:15px;line-height:32px;color:var(--muted)}

/* segments */
.segment{top:958px;width:320px;height:320px;border-radius:50%;text-align:center;color:var(--white);font-family:"Roboto",sans-serif;box-shadow:0 24px 18px -16px rgba(0,0,0,.18)}
.segment svg{margin-top:72px}
.segment h3{font-weight:400;font-size:20px;line-height:27px;margin-top:18px}
.segment .btn-outline{display:inline-block;margin-top:16px;border:2px solid currentColor;border-radius:22px;padding:7px 28px;font-size:15px;background:rgba(255,255,255,.1)}
.seg-couples{left:96px;background:var(--grey-light);border:4px solid #e2e2e2;color:var(--text)}
.seg-couples .btn-outline{border-color:#777;background:var(--white)}
.seg-friends{left:439px;background:var(--gold);border:4px solid #e4d7b8}
.seg-moms{left:780px;background:var(--grey-mid);border:4px solid #dcdcdc}

/* products */
.band-grey{left:0;top:1366px;width:1200px;height:516px;background:var(--grey-light)}
.section-title{left:0;width:1200px;text-align:center;font-family:"Roboto",sans-serif;font-weight:400;font-size:36px;color:var(--text)}
.arrows{left:1052px;top:1420px;display:flex;gap:14px}
.card{width:244px;height:350px;background:var(--white);border:1px solid var(--line)}
.card .photo{height:206px}
.card h4{font-size:17px;font-weight:600;margin:28px 0 0 22px}
.card .sub{font-size:10px;color:#aaa;margin:4px 0 0 22px}
.card .row{display:flex;justify-content:space-between;align-items:center;margin:18px 14px 0 22px}
.price{color:var(--gold);font-size:22px}
.btn-shop{background:var(--grey-btn);color:var(--white);font-size:12px;border-radius:16px;padding:7px 22px}

/* why us */
.why-box{left:97px;top:2481px;width:1008px;height:352px;background:#f1f1f1;border:1px solid var(--line)}
.feature{width:320px}
.feature .icon{position:absolute;left:0;top:0;width:76px;height:76px;border-radius:50%;display:flex;align-items:center;justify-content:center}
.feature h5{margin-left:98px;padding-top:4px;font-size:17px;font-weight:600;color:var(--text);white-space:nowrap}
.feature p{margin-left:98px;margin-top:8px;font-size:11px;line-height:18px;color:var(--muted);white-space:nowrap}
.icon.grey{background:var(--grey-mid)}
.icon.gold{background:var(--gold)}

/* newsletter */
.newsletter{left:0;top:2892px;width:1200px;height:261px;background:var(--gold-soft);color:var(--white);text-align:center}
.newsletter h2{font-size:26px;font-weight:700;margin-top:54px;letter-spacing:.5px}
.newsletter p{font-size:16px;margin-top:12px;opacity:.95}
.signup{position:absolute;left:251px;top:154px;display:flex}
.signup .field{width:539px;height:48px;background:var(--white);color:#999;font-size:12px;text-align:left;padding:16px 22px}
.signup .submit{width:169px;height:48px;background:#5c5c5c;color:var(--white);font-size:15px;font-weight:700;padding-top:13px}

/* footer */
.footer{left:0;top:3153px;width:1200px;height:319px;background:#f0f0f0}
.footer .brand-name{position:absolute;left:128px;top:46px;font-size:28px}
.foot-col{position:absolute;top:58px}
.foot-col h6{font-family:"Roboto",sans-serif;font-weight:500;font-size:16px;color:var(--gold)}
.foot-col ul{list-style:none;margin-top:22px}
.foot-col li{font-size:13px;color:var(--text);line-height:32px;display:flex;align-items:center;gap:12px;white-space:nowrap}
.social-dot{width:28px;height:28px;border-radius:50%;background:#555;display:inline-block}
.footer-bottom{left:0;top:3472px;width:1200px;height:78px;background:var(--white)}
.footer-bottom .copy{position:absolute;left:147px;top:30px;font-size:11px;color:var(--text)}
.pay{position:absolute;top:22px;height:32px;border-radius:3px}
</style>
</head>
<body>

<div class="abs topbar">
  <span class="lang">Language:</span>
  <span style="left:705px">My Account</span>
  <span style="left:817px">Register</span>
  <span style="left:906px">Log In</span>
  <div class="cart">
    <svg width="22" height="22" viewBox="0 0 22 22" fill="none" stroke="#fff" stroke-width="2"><path d="M2 4h3l3 11h10l2-8H7"/><circle cx="9" cy="19" r="1.5"/><circle cx="17" cy="19" r="1.5"/></svg>
    0 items
  </div>
</div>

<header class="abs header">
  <div class="brand-badge"><span class="brand-name">Velvet Loom</span></div>
  <a class="nav active" style="left:428px">HOME</a>
  <a class="nav" style="left:516px">ABOUT US</a>
  <a class="nav" style="left:634px">PRODUCTS</a>
  <a class="nav" style="left:760px">SHOP NOW</a>
  <a class="nav" style="left:888px">WHY US</a>
  <a class="nav" style="left:989px">CONTACT</a>
</header>

<section class="abs hero">
  <div class="hero-photo" role="img" aria-label="Embroidered purple and white towels tied with ribbons, personalized with names"></div>
  <div class="hero-badge">
    <h2>Embroidered<br>Pillows &amp; Cushions</h2>
    <p>Sociosqu ad litora torquent per conubia nostra per inceptos hymenaeos</p>
    <a class="btn-dark">Shop Now &rsaquo;</a>
  </div>
  <div class="dots"><i class="on"></i><i></i><i></i><i></i></div>
  <svg class="hero-curve" width="1200" height="120" viewBox="0 0 1200 120">
    <path d="M0 40 Q600 150 1200 40 L1200 120 L0 120 Z" fill="#d8d8d8"/>
    <path d="M0 70 Q600 140 1200 60 L1200 120 L0 120 Z" fill="#ffffff"/>
  </svg>
</section>

<h1 class="abs welcome-title">Welcome to Velvet Loom</h1>
<p class="abs welcome-text">ue et malesuada iaculis ipsum dui aliquet felis at cursus magna nisl nec elit Praesent elementum elit at tellus nec ultricies sit amet porttitor mattis enim In massa libero interdum nec interdum vel blandit sed nulla In ullamcorper est eget tempor cursus neque mi consectetuer mi a ultricies</p>

<div class="abs segment seg-couples">
  <svg width="80" height="70" viewBox="0 0 80 70" fill="none" stroke="#444" stroke-width="3"><circle cx="30" cy="44" r="20"/><circle cx="50" cy="44" r="20"/><path d="M40 6 l6 6 -6 6 -6 -6z"/></svg>
  <h3>Lovers and<br>Marring Couples</h3>
  <a class="btn-outline">Click here</a>
</div>
<div class="abs segment seg-friends">
  <svg width="80" height="70" viewBox="0 0 80 70" fill="#fff"><path d="M40 30 L10 12 Q4 30 10 46 Z"/><path d="M40 30 L70 12 Q76 30 70 46 Z"/><circle cx="40" cy="30" r="7"/><path d="M36 34 L24 64 L30 62 L40 40 Z"/><path d="M44 34 L56 64 L50 62 L40 40 Z"/></svg>
  <h3>Close friends wishing<br>to give unique gifts</h3>
  <a class="btn-outline">Click here</a>
</div>
<div class="abs segment seg-moms">
  <svg width="80" height="70" viewBox="0 0 80 70" fill="none" stroke="#fff" stroke-width="3"><path d="M6 6h8l6 16h44a22 20 0 0 1-44 4"/><path d="M40 22 V4 a24 20 0 0 1 24 18"/><circle cx="26" cy="58" r="7"/><circle cx="58" cy="58" r="7"/></svg>
  <h3>Moms with new born<br>baby personalized gifts</h3>
  <a class="btn-outline">Click here</a>
</div>

<div class="abs band-grey"></div>
<h2 class="abs section-title" style="top:1408px">Featured Products</h2>
<div class="abs arrows">
  <svg width="14" height="22" viewBox="0 0 14 22" fill="none" stroke="#999" stroke-width="2"><path d="M11 3 L4 11 L11 19"/></svg>
  <svg width="14" height="22" viewBox="0 0 14 22" fill="none" stroke="#999" stroke-width="2"><path d="M3 3 L10 11 L3 19"/></svg>
</div>

<article class="abs card" style="left:107px;top:1475px">
  <div class="photo" role="img" aria-label="Grey embroidered pillow with a name stitched in blue and a ribbon" style="background:linear-gradient(135deg,#7b7b80,#5d5d62)"></div>
  <h4>Embroidered Pillows</h4><p class="sub">sociosqu ad litora torquent conubia</p>
  <div class="row"><span class="price">$25.99</span><a class="btn-shop">Shop Now</a></div>
</article>
<article class="abs card" style="left:362px;top:1475px">
  <div class="photo" role="img" aria-label="Folded white and pink towels with embroidered names" style="background:linear-gradient(135deg,#e6e3e6,#b94a7a)"></div>
  <h4>Towels</h4><p class="sub">sociosqu ad litora torquent conubia</p>
  <div class="row"><span class="price">$25.99</span><a class="btn-shop">Shop Now</a></div>
</article>
<article class="abs card" style="left:617px;top:1475px">
  <div class="photo" role="img" aria-label="Coral and white bathrobes with embroidered names" style="background:linear-gradient(135deg,#e67a6a,#eee9ea)"></div>
  <h4>Bathrobes</h4><p class="sub">sociosqu ad litora torquent conubia</p>
  <div class="row"><span class="price">$25.99</span><a class="btn-shop">Shop Now</a></div>
</article>
<article class="abs card" style="left:872px;top:1475px">
  <div class="photo" role="img" aria-label="Purple and white baby gift towels with embroidered names" style="background:linear-gradient(135deg,#8a6f95,#ebe7ea)"></div>
  <h4>Baby gifts</h4><p class="sub">sociosqu ad litora torquent conubia</p>
  <div class="row"><span class="price">$25.99</span><a class="btn-shop">Shop Now</a></div>
</article>

<h2 class="abs section-title" style="top:1922px">New Arrivals</h2>

<article class="abs card" style="left:100px;top:1988px">
  <div class="photo" role="img" aria-label="White pillow with embroidered little man text" style="background:linear-gradient(135deg,#f2f2f2,#bdbdbd)"></div>
  <h4>Embroidered Pillows</h4><p class="sub">sociosqu ad litora torquent conubia</p>
  <div class="row"><span class="price">$25.99</span><a class="btn-shop">Shop Now</a></div>
</article>
<article class="abs card" style="left:355px;top:1988px">
  <div class="photo" role="img" aria-label="Red and white towels with gold embroidered names" style="background:linear-gradient(135deg,#9e2a2f,#efe6e0)"></div>
  <h4>Towels</h4><p class="sub">sociosqu ad litora torquent conubia</p>
  <div class="row"><span class="price">$25.99</span><a class="btn-shop">Shop Now</a></div>
</article>
<article class="abs card" style="left:610px;top:1988px">
  <div class="photo" role="img" aria-label="Cream pillow with embroidered calendar and date" style="background:linear-gradient(135deg,#ece6da,#8a2f32)"></div>
  <h4>Pillows</h4><p class="sub">sociosqu ad litora torquent conubia</p>
  <div class="row"><span class="price">$25.99</span><a class="btn-shop">Shop Now</a></div>
</article>
<article class="abs card" style="left:865px;top:1988px">
  <div class="photo" role="img" aria-label="Lavender and white baby towels with embroidered name" style="background:linear-gradient(135deg,#9c86a8,#e9e5ea)"></div>
  <h4>Baby gifts</h4><p class="sub">sociosqu ad litora torquent conubia</p>
  <div class="row"><span class="price">$25.99</span><a class="btn-shop">Shop Now</a></div>
</article>

<h2 class="abs section-title" style="top:2418px">Why Choose Us</h2>
<div class="abs why-box"></div>
<svg class="abs" style="left:440px;top:2520px" width="320" height="270" viewBox="0 0 320 270" fill="none" stroke="#888" stroke-width="1.5">
  <path d="M36 12 H88 V80"/><path d="M36 256 H88 V190"/>
  <path d="M284 12 H232 V80"/><path d="M284 256 H232 V190"/>
  <g fill="#888" stroke="none"><circle cx="36" cy="12" r="4"/><circle cx="36" cy="256" r="4"/><circle cx="284" cy="12" r="4"/><circle cx="284" cy="256" r="4"/></g>
</svg>
<div class="abs brand-name" style="left:440px;top:2634px;width:320px;text-align:center;font-size:34px">Velvet Loom</div>

<div class="abs feature" style="left:140px;top:2530px">
  <div class="icon grey"><svg width="34" height="34" viewBox="0 0 34 34" fill="none" stroke="#fff" stroke-width="3"><path d="M6 22 V17 a11 11 0 0 1 22 0 V22"/><rect x="4" y="19" width="6" height="9" rx="2" fill="#fff"/><rect x="24" y="19" width="6" height="9" rx="2" fill="#fff"/></svg></div>
  <h5>Support</h5><p>Passages of Lorem Ipsum available,<br>but the majority.</p>
</div>
<div class="abs feature" style="left:140px;top:2689px">
  <div class="icon grey"><svg width="34" height="34" viewBox="0 0 34 34" fill="none" stroke="#fff" stroke-width="3"><path d="M10 6 V28"/><path d="M17 6 V28"/><path d="M24 6 V28"/></svg></div>
  <h5>Quality work</h5><p>Passages of Lorem Ipsum available,<br>but the majority.</p>
</div>
<div class="abs feature" style="left:757px;top:2530px">
  <div class="icon gold"><svg width="36" height="30" viewBox="0 0 36 30" fill="#fff"><rect x="2" y="6" width="20" height="14"/><path d="M22 10 h7 l5 5 v5 h-12z"/><circle cx="9" cy="23" r="4"/><circle cx="28" cy="23" r="4"/></svg></div>
  <h5>Delivery and return</h5><p>Passages of Lorem Ipsum available,<br>but the majority.</p>
</div>
<div class="abs feature" style="left:757px;top:2689px">
  <div class="icon gold"><svg width="36" height="30" viewBox="0 0 36 30" fill="#fff"><circle cx="18" cy="8" r="6"/><path d="M8 28 a10 10 0 0 1 20 0z"/><circle cx="7" cy="12" r="4"/><circle cx="29" cy="12" r="4"/></svg></div>
  <h5>VL Warranty</h5><p>Passages of Lorem Ipsum available,<br>but the majority.</p>
</div>

<section class="abs newsletter">
  <h2>NEWSLETTER SUBSCRIPTION</h2>
  <p>Register your email address to get information about us</p>
  <div class="signup"><div class="field">EMAIL ADDRESS</div><div class="submit">SUBSCRIBE</div></div>
</section>

<footer class="abs footer">
  <span class="brand-name">Velvet Loom</span>
  <div class="foot-col" style="left:338px">
    <h6>Menu Links</h6>
    <ul><li>Home</li><li>Products</li><li>Stores</li><li>Locations</li><li>Testimonials</li><li>Contact Us</li></ul>
  </div>
  <div class="foot-col" style="left:535px">
    <h6>Quick Contact</h6>
    <ul>
      <li><svg width="22" height="16" viewBox="0 0 22 16" fill="none" stroke="var(--gold)" stroke-width="1.5"><rect x="1" y="1" width="20" height="14"/><path d="M1 1 L11 9 L21 1"/></svg>Velvet.loom.studio@plumemail.net</li>
      <li><svg width="22" height="20" viewBox="0 0 22 20" fill="none" stroke="var(--gold)" stroke-width="1.5"><path d="M5 2 h4 l2 5 -3 2 a10 10 0 0 0 5 5 l2 -3 5 2 v4 a2 2 0 0 1 -2 2 A16 16 0 0 1 3 4 a2 2 0 0 1 2 -2z"/></svg>+966 54 312 9067</li>
    </ul>
  </div>
  <div class="foot-col" style="left:878px">
    <h6>Get In Touch</h6>
    <ul style="margin-top:16px">
      <li style="line-height:42px"><span class="social-dot"></span>Friendbook</li>
      <li style="line-height:42px"><span class="social-dot"></span>Picturely</li>
      <li style="line-height:42px"><span class="social-dot"></span>Chirper</li>
    </ul>
  </div>
</footer>

<div class="abs footer-bottom">
  <span class="copy">© 2017 Company Name &nbsp;|&nbsp; All Rights Reserved</span>
  <span class="pay" style="left:935px;width:30px;background:#777"></span>
  <span class="pay" style="left:978px;width:40px;background:#e9e9f0;border:1px solid #ccc"></span>
  <span class="pay" style="left:1024px;width:40px;background:#c9463d"></span>
  <span class="pay" style="left:1070px;width:40px;background:#e6e9ee;border:1px solid #ccc"></span>
</div>

</body>
</html>
```